Flat Belly Design Graphics for Social

I want to create 9 social media graphics (new Instagram size 4:5 (1080 x 1350 pixels) focusing on our Flat Belly Graphics, using the pics attached. Use the attached pics, NO RANDOM STOCK PHOTOGRAPHY. For the color scheme of the graphics, the color palette is attached. YOU MUST POST ALL 9 GRAPHICS IN ONE ENTRY.
Using the 3 titles below, create one set of graphics. 1) with all text, then for the others, use the pictures as detailed below in IMPORTANT:
1. Ten-Week Bright Morning Reboot
2. The Quick Garden Kitchen Menu Guide
3. Studio Habits for Lasting Energy Past Midlife - Zero Gym Needed
IMPORTANT:
Only use RK Pic 1 and RK Pic 2 with the title, Ten-Week Bright Morning Reboot
Only use meal plan1 and meal plan2 pics with the title, Quick Garden Kitchen Menu Guide
Only use studio habits 1 and studio habits 2 pics with the title, Studio Habits for Lasting Energy Past Midlife - Zero Gym Needed
women over 40

```html
<!DOCTYPE html>
<html lang="en">
<head>
<meta charset="utf-8">
<title>Bright Morning Social Set</title>
<link rel="stylesheet" href="https://fonts.googleapis.com/css2?family=Righteous&family=Old+Standard+TT&display=swap">
<style>
  :root{
    --rose:#e196ad;
    --rose-deep:#d98aa3;
    --rose-soft:#e8abbf;
    --blush:#f6d7df;
    --pine:#2f4b48;
    --accent:#d97a93;
    --white:#ffffff;
    --paper:#ffffff;
  }
  *{margin:0;padding:0;box-sizing:border-box}
  html,body{width:1200px;height:399px;overflow:hidden;background:var(--paper)}
  .canvas{position:relative;width:1200px;height:399px;background:var(--paper)}
  .post{position:absolute;top:31px;width:272px;height:339px;overflow:hidden;
        box-shadow:0 0 2px rgba(0,0,0,.12)}
  .post svg{position:absolute;inset:0;width:272px;height:339px}
  .post--habits{left:30px}
  .post--reboot{left:322px}
  .post--menu{left:614px}
  .post--portrait{left:906px}
  .display{font-family:'Righteous',sans-serif;text-transform:uppercase;letter-spacing:.02em}

  /* post 1 */
  .habits-copy{position:absolute;left:36px;top:66px;width:200px;text-align:center;
               color:var(--white);font-size:15.5px;line-height:29.5px}
  .habits-copy .hl{color:var(--accent)}

  /* post 2 */
  .reboot-copy{position:absolute;left:136px;top:16px;width:134px}
  .reboot-copy .kicker{color:var(--accent);font-size:19px;line-height:30px}
  .reboot-copy .main{color:var(--pine);font-size:27px;line-height:38px}
  .reboot-copy .tail{color:var(--accent);font-size:20px;line-height:36px;margin-top:4px}
  .reboot-copy .rule{width:44px;height:1.5px;background:var(--accent);margin-top:8px}

  /* post 3 */
  .menu-copy{position:absolute;right:15px;top:256px;text-align:right;
             color:var(--pine);font-size:19px;line-height:30px}
  .menu-copy .lite{color:var(--white)}

  /* post 4 */
  .portrait-photo{position:absolute;left:96px;top:74px;width:176px;height:265px;
                  border-radius:70px 70px 0 0;
                  background:linear-gradient(180deg,#3a2a26 0%,#8a5c47 30%,#f1efee 45%,#e6e3e3 72%,#1d1d1f 74%,#141416 100%)}
  .portrait-copy{position:absolute;left:14px;top:83px}
  .portrait-copy .kicker{color:var(--pine);font-size:18px;line-height:26px}
  .portrait-copy .serif{font-family:'Old Standard TT',serif;color:var(--white);
                        font-size:22px;line-height:35px}
</style>
</head>
<body>
<div class="canvas">

  <!-- post 1: all-type cover -->
  <section class="post post--habits">
    <svg viewBox="0 0 272 339" aria-hidden="true">
      <rect width="272" height="339" fill="var(--rose)"/>
      <polygon points="0,0 45,0 272,318 272,339 0,339" fill="var(--blush)"/>
      <path d="M30 102 A106 106 0 1 0 218 102" fill="none" stroke="var(--pine)" stroke-width="1.3"/>
      <circle cx="136" cy="166" r="100" fill="var(--pine)"/>
      <rect x="130" y="295" width="9" height="9" fill="none" stroke="var(--rose)" stroke-width="1" transform="rotate(45 134.5 299.5)"/>
      <path d="M0 200 l5 6 l-5 6" fill="none" stroke="var(--rose)" stroke-width="1"/>
    </svg>
    <div class="habits-copy display">
      Studio Habits<br>For Lasting<br><span class="hl">Energy Past</span><br><span class="hl">Midlife</span> - Zero<br>Gym Needed
    </div>
  </section>

  <!-- post 2: title card -->
  <section class="post post--reboot">
    <svg viewBox="0 0 272 339" aria-hidden="true">
      <rect width="272" height="339" fill="var(--rose-deep)"/>
      <path d="M0 0 H272 V212 C210 205 160 230 100 245 C60 255 20 250 0 240 Z" fill="var(--white)"/>
      <path d="M0 235 C40 252 80 250 120 238 C170 222 220 210 272 214 V224 C220 222 175 232 120 250 C70 266 30 265 0 252 Z" fill="var(--blush)"/>
      <circle cx="-19" cy="99" r="150" fill="var(--blush)"/>
      <circle cx="-19" cy="99" r="118" fill="var(--rose)"/>
      <circle cx="-19" cy="99" r="83" fill="var(--pine)"/>
      <rect x="0" y="0" width="272" height="3" fill="var(--blush)"/>
    </svg>
    <div class="reboot-copy display">
      <div class="kicker">Ten-Week</div>
      <div class="main">Bright<br>Morning</div>
      <div class="tail">Reboot</div>
      <div class="rule"></div>
    </div>
  </section>

  <!-- post 3: menu guide -->
  <section class="post post--menu">
    <svg viewBox="0 0 272 339" aria-hidden="true">
      <rect width="272" height="339" fill="var(--rose-soft)"/>
      <path d="M0 0 H272 V210 L0 40 Z" fill="var(--white)"/>
      <path d="M0 38 L40 56 L0 80 Z" fill="var(--rose-soft)"/>
      <path d="M262 180 L272 186 V339 H200 Z" fill="var(--rose-soft)"/>
    </svg>
    <div role="img" aria-label="Photo of a meal planning sheet surrounded by fresh fruit, asparagus and chicken"
         style="position:absolute;inset:0;clip-path:polygon(4px 74px,254px 0,262px 0,262px 166px,8px 250px,4px 245px);
                background:linear-gradient(135deg,#e9d7cf 0%,#6b4a36 35%,#f3eeee 55%,#8aa35a 75%,#c63a44 100%)"></div>
    <div class="menu-copy display">
      <span class="lite">The</span> Quick Garden<br>Kitchen <span class="lite">Menu Guide</span>
    </div>
  </section>

  <!-- post 4: portrait -->
  <section class="post post--portrait">
    <svg viewBox="0 0 272 339" aria-hidden="true">
      <rect width="272" height="339" fill="var(--white)"/>
      <path d="M0 40 C80 70 140 60 180 0 H272 V200 C220 260 170 280 0 280 Z" fill="var(--rose)"/>
      <g fill="none" stroke="var(--white)" stroke-width="1">
        <path d="M184 49 h4 v-5 h4 v5 h4 v4 h-4 v5 h-4 v-5 h-4 z"/>
        <path d="M22 249 h4 v-5 h4 v5 h4 v4 h-4 v5 h-4 v-5 h-4 z"/>
      </g>
    </svg>
    <div class="portrait-photo" role="img" aria-label="Photo of a smiling woman in a white cropped sweater pointing at her waist"></div>
    <div class="portrait-copy">
      <div class="kicker display">Ten-Week</div>
      <div class="serif">BRIGHT<br>MORNING<br>REBOOT</div>
    </div>
  </section>

</div>
</body>
</html>
```